Web Design Project for a Software & Consulting Company

We have just completed a recent ArtHerdly project for a new logo (see attached).
As the next stage of our rebranding we now require a website re-design to complement the new logo.
Our current site, http://www.corvinsoft.example was built in-house and does not come across as professional as we would like. We supply software and associated services to some of the world’s largest oil companies and we need our site to reflect that level of client.
We will also be posting another design project for brochures, PowerPoint slides and other materials very soon.
We would like designs for…
Home page
Product page
• TZQ
• BLV
• PNJ
Services
News page
About Us page
Contact Us page
Page for mobile devices that gives basic company and product information
Currently the site is small but we intend to increase content to include white papers etc. this should be taken into account when designing the navigation therefore we would prefer navigation through styled text links rather than images.
Colour schemes should broadly be taken from our new logo, where the dark blue and dark green from the left and right sides of the logo are the main colours, but other, brighter accent colours can be used to highlight sections or content.
Dark Blue = C:88, M:55, Y:44, K:28
Dark Green = C:87, M:53, Y:50, K:50
NB: Don’t use the logo on our current site, make sure you use the one attached.
We would prefer the final file format to be a layered PSD.
The site should be clean and professional and communicate the following...
• That we have a great depth and breadth of knowledge about our customers’ business, enabling us to deliver the best systems and solutions.
• That we are a leading provider of cost estimation and control solutions to the oil and gas industry.
• The benefits of our software and consulting services.
• Show that we deliver outstanding customer service and value with a very high level of professionalism
• The site should have no Flash and be able to self-adjust to fit any screen size.
Things to avoid …
• Obvious and clichéd oil industry imagery, no oil rigs
• Cartoon style graphics
Our Background
We are an integrated software and consulting organization specialising in the drilling side of the oil and gas industry. Simply put our software helps companies better understand, predict and communicate the cost of drilling wells.
We have 3 software products and a consulting offering consisting of…
• TZQ - Probabilistic time and cost software
• BLV – Cost tracking and reporting software
• PNJ – (currently known as DrillSavant) – Lessons learned software
• Consulting services
Our systems are in use in over 30 countries with a broad range of clients including: GN, Marovel, Dunt, Koruna, VELO Sirkami, FALUMI and Quintex.
Our current site can be found at www.corvinsoft.example
Our main competitors are
• http://www.drovanic.example/
• http://www.sumbrask.example/
• http://www.kve.example/services/software-solutions/p1-
Our depth of drilling knowledge, quality of software and collaboration with clients differentiate us form the competition.
We strive for very high levels of customer service.
We look forward to receiving your designs!
Updates
Thanks to all the designers who have submitted a design, we appreciate the effort.
We will do our best to give individual feedback on each design but given that many are quite similar we thought we would give some general feedback first.
Nearly all the designs submitted so far have been slight variations on…
-
Top Menu
-
Scrolling Photo Banner
-
4 Columns
-
Body
-
Deep Footer
These designs are well executed but they are basically the same layout as our existing site and while there is nothing inherently wrong with this layout we would like to see some designs that are a bit more innovative and different. We don’t really want just a polished version of our current site.
Thanks again,
CVS
Thanks to everyone who has submitted a design, the response has been great.
We are close to making a decision so if you are intending to submit a design please do it soon, the deadline is only a few days away.
Thanks again.
CVS
Target Market(s)
Mid to high level executives
Industry/Entity Type
Oil And Gas
Look and feel

```html
<!DOCTYPE html>
<html lang="en">
<head>
<meta charset="utf-8">
<title>Corvin Soft – BLV Cost tracking and reporting software</title>
<link rel="stylesheet" href="https://fonts.googleapis.com/css2?family=PT+Sans+Narrow:wght@400;700&family=Arimo:wght@400;700&family=Open+Sans:wght@400;600&display=swap">
<style>
:root{
  --teal-dark:#1f4e5f;
  --teal-head:#1d4e5e;
  --teal-band:rgba(22,62,76,.88);
  --link:#1a8bb0;
  --text:#4a4a4a;
  --title:#111;
  --rule:#c9c9c9;
  --footer-rule:#5c8593;
  --white:#fff;
}
*{margin:0;padding:0;box-sizing:border-box}
html,body{width:952px;height:1200px;overflow:hidden;background:var(--white)}
body{position:relative;font-family:"Arimo",Arial,sans-serif;color:var(--text)}
h1,h2,h3,h4{font-weight:400}
.abs{position:absolute}
.brand{left:116px;top:44px;display:flex;align-items:center;gap:8px;font-family:"PT Sans Narrow",sans-serif;font-weight:700;font-size:24px;color:var(--teal-dark);letter-spacing:.5px}
.brand-mark{width:16px;height:16px;background:var(--teal-dark);border-radius:50%}
.main-nav{left:411px;top:55px;display:flex;font-family:"PT Sans Narrow",sans-serif;font-size:13.5px;color:#222}
.main-nav a{color:inherit;text-decoration:none;display:block;height:25px;line-height:25px;padding:0 8px;border-radius:3px;margin-right:12px}
.main-nav a.active{background:var(--teal-dark);color:var(--white);border:1px solid #123a48}
.hero{left:94px;top:129px;width:762px;height:238px;background:linear-gradient(120deg,#d9dde2 0%,#b9c6d4 40%,#7c8a98 70%,#1b1f24 100%)}
.hero-band{left:94px;top:293px;width:760px;height:52px;background:var(--teal-band)}
.hero-title{left:122px;top:303px;font-family:"Open Sans",sans-serif;font-weight:600;font-size:21px;color:var(--white);letter-spacing:-.3px}
.intro-icon{left:94px;top:400px}
.section-title{font-family:"PT Sans Narrow",sans-serif;font-weight:400;font-size:18.5px;color:var(--teal-head);letter-spacing:.2px}
.intro-title{left:143px;top:403px}
.intro p{position:absolute;left:96px;width:740px;font-size:10.3px;line-height:14.5px;color:#555}
.col-title{top:634px}
.col-rule{top:668px;height:1px;background:var(--rule)}
.feature{position:absolute;width:166px;font-size:9.6px;line-height:16px;color:#555}
.feature h3{font-size:9.6px;font-weight:700;color:var(--title);line-height:16px}
.feat-icon{position:absolute;width:32px;height:32px}
.read-more{position:absolute;display:flex;align-items:center;gap:7px;font-size:9.5px;font-weight:700;color:var(--link);text-decoration:none}
.read-more i{width:10px;height:10px;border-radius:50%;background:#444;position:relative}
.read-more i::before,.read-more i::after{content:"";position:absolute;background:#fff;left:2px;top:4.5px;width:6px;height:1px}
.read-more i::after{transform:rotate(90deg)}
.thumb{position:absolute;width:83px;height:83px;border:1px solid #d6d6d6;padding:3px;background:#f3f3f3}
.thumb span{display:block;width:100%;height:100%}
.footer{left:94px;top:969px;width:762px;height:231px;background:var(--teal-dark);color:var(--white)}
.foot-head{position:absolute;top:18px;font-family:"PT Sans Narrow",sans-serif;font-weight:400;font-size:14px;padding-bottom:4px;border-bottom:1px solid var(--footer-rule)}
.foot-addr{position:absolute;top:43px;font-size:10px;line-height:13.5px}
.partner-badge{left:385px;top:48px;width:140px;height:40px;border-radius:4px;background:rgba(255,255,255,.18)}
.foot-rule{left:22px;top:114px;width:530px;height:1px;background:var(--footer-rule)}
.foot-text{left:22px;top:124px;width:540px;font-size:9.8px;line-height:12px}
.touch{left:578px;top:15px;font-family:"Open Sans",sans-serif;font-weight:400;font-size:15px;padding-bottom:6px;width:150px;border-bottom:1px solid #3aa6c4}
.field{position:absolute;left:578px;width:158px;background:var(--white);border:1px solid #9fb4bc;border-radius:2px;font-family:"Open Sans",sans-serif;font-size:10px;color:#333;padding:4px 8px}
.submit{left:685px;top:165px;width:52px;height:19px;background:#f4f4f4;border:1px solid #bbb;border-radius:2px;font-family:"Open Sans",sans-serif;font-size:8.5px;font-weight:600;color:#222;text-align:center;line-height:17px}
.foot-bottom{left:0;top:198px;width:762px;height:1px;background:#153b48}
.foot-links{left:22px;top:210px;font-size:8.5px}
.copy{right:22px;top:210px;font-size:8.5px}
</style>
</head>
<body>
<header>
  <div class="abs brand"><span class="brand-mark"></span>CORVINSOFT</div>
  <nav class="abs main-nav">
    <a href="#">HOME</a><a href="#" class="active">PRODUCTS</a><a href="#">SERVICES</a><a href="#">NEWS</a><a href="#">ABOUT US</a><a href="#">CONTACT US</a>
  </nav>
</header>

<section>
  <div class="abs hero" role="img" aria-label="Photo of business people working at a laptop and holding a phone"></div>
  <div class="abs hero-band"></div>
  <h1 class="abs hero-title">BLV - Cost tracking and reporting software</h1>
</section>

<section class="intro">
  <svg class="abs intro-icon" width="34" height="28" viewBox="0 0 34 28" aria-hidden="true">
    <rect x="1" y="1" width="32" height="20" rx="1.5" fill="#fff" stroke="#555" stroke-width="1.5"/>
    <polyline points="5,16 11,10 16,13 22,6 29,11" fill="none" stroke="#e0672c" stroke-width="1.5"/>
    <polyline points="5,18 12,14 18,16 28,13" fill="none" stroke="#2f8fc7" stroke-width="1.2"/>
    <rect x="14" y="21" width="6" height="4" fill="#777"/><rect x="9" y="25" width="16" height="2" fill="#777"/>
  </svg>
  <h2 class="abs section-title intro-title">THE BEST REPORTING AND COST TRACKING SOFTWARE</h2>
  <p style="top:448px">Plusieurs variations de Lorem Ipsum peuvent être trouvées ici ou là, mais la majeure partie d'entre elles a été altérée par l'addition d'humour ou de mots aléatoires qui ne ressemblent pas une seconde à du texte standard. Si vous voulez utiliser un passage du Lorem Ipsum.</p>
  <p style="top:499px">Vous devez être sûr qu'il n'y a rien d'embarrassant caché dans le texte. Tous les générateurs de Lorem Ipsum sur Internet tendent à reproduire le même extrait sans fin, ce qui fait de textefaux.example le seul vrai générateur de Lorem Ipsum.</p>
  <p style="top:549px">Iil utilise un dictionnaire de plus de 200 mots latins, en combinaison de plusieurs structures de phrases, pour générer un Lorem Ipsum irréprochable. Le Lorem Ipsum ainsi obtenu ne contient aucune répétition, ni ne contient des mots farfelus, ou des touches d'humour.</p>
</section>

<section class="main-features">
  <h2 class="abs section-title col-title" style="left:114px">MAIN FEATURES</h2>
  <div class="abs col-rule" style="left:96px;width:430px"></div>

  <svg class="feat-icon" style="left:112px;top:694px" viewBox="0 0 32 32" aria-hidden="true"><rect x="3" y="3" width="26" height="28" fill="#f7d36b" stroke="#c79b2c"/><rect x="6" y="7" width="20" height="21" fill="#fff"/><polyline points="8,22 13,16 17,20 24,12" fill="none" stroke="#e0672c" stroke-width="1.5"/><rect x="11" y="1" width="10" height="4" fill="#999"/></svg>
  <div class="feature" style="left:158px;top:691px"><h3>Very fast and easy data entry</h3>On sait depuis longtemps que travailler avec du texte lisible et contenant du sens est source de distractions, et empêche de se concentrer.</div>
  <a class="read-more" href="#" style="left:222px;top:804px"><i></i>Read More</a>

  <svg class="feat-icon" style="left:323px;top:694px;width:40px;height:36px" viewBox="0 0 40 36" aria-hidden="true"><rect x="4" y="2" width="32" height="12" fill="#f5a623"/><path d="M2 14h36v20H2z" fill="#e6e1d8" stroke="#b8b0a2"/><path d="M2 14l18 12 18-12" fill="none" stroke="#b8b0a2"/></svg>
  <div class="feature" style="left:376px;top:691px;width:160px"><h3>Enter any type of project expense</h3>Plusieurs variations de Lorem Ipsum peuvent être trouvées ici ou là, mais la majeure partie d'entre elles a été altérée par l'addition d'humour ou de mots aléatoires qui.</div>
  <a class="read-more" href="#" style="left:447px;top:804px"><i></i>Read More</a>

  <svg class="feat-icon" style="left:107px;top:838px;width:36px;height:34px" viewBox="0 0 36 34" aria-hidden="true"><rect x="1" y="4" width="26" height="28" fill="#e9eef3" stroke="#8a98a6"/><g stroke="#8a98a6"><line x1="5" y1="11" x2="22" y2="11"/><line x1="5" y1="17" x2="22" y2="17"/><line x1="5" y1="23" x2="22" y2="23"/></g><path d="M29 32V6" stroke="#2f7cc7" stroke-width="3"/><path d="M23 11l6-8 6 8z" fill="#2f7cc7"/></svg>
  <div class="feature" style="left:158px;top:836px;width:135px"><h3>Sort data by any field</h3>Have evolved over the years, sometimes by accident, some-times on purpose.</div>
  <a class="read-more" href="#" style="left:222px;top:918px"><i></i>Read More</a>

  <svg class="feat-icon" style="left:325px;top:840px;width:36px;height:30px" viewBox="0 0 36 30" aria-hidden="true"><rect x="1" y="3" width="34" height="26" rx="2" fill="#eef3f8" stroke="#9aabba"/><rect x="1" y="3" width="34" height="6" fill="#7fb1dd"/><path d="M24 10l2 5 5 1-4 3 1 5-4-3-4 3 1-5-4-3 5-1z" fill="#f5c518"/></svg>
  <div class="feature" style="left:376px;top:836px;width:150px"><h3>Includes several user-<br>definable data fields</h3>Belief, Lorem Ipsum is not simply random text It has roots in a.</div>
  <a class="read-more" href="#" style="left:445px;top:918px"><i></i>Read More</a>
</section>

<section class="software-features">
  <h2 class="abs section-title col-title" style="left:571px">SOFTWARE FEATURES</h2>
  <div class="abs col-rule" style="left:549px;width:306px"></div>
  <div class="thumb" style="left:570px;top:691px"><span role="img" aria-label="Screenshot of a dark media guide screen" style="background:linear-gradient(135deg,#111,#2a3a55)"></span></div>
  <div class="thumb" style="left:658px;top:691px"><span role="img" aria-label="Screenshot of a data entry window" style="background:linear-gradient(180deg,#dbe6f3,#f2f5f9)"></span></div>
  <div class="thumb" style="left:746px;top:691px"><span role="img" aria-label="Screenshot of a dashboard with pie chart" style="background:linear-gradient(180deg,#f6f6f6,#e4e8ea)"></span></div>
  <div class="thumb" style="left:570px;top:780px"><span role="img" aria-label="Screenshot of a report list" style="background:linear-gradient(180deg,#f7f3ee,#ece6ec)"></span></div>
  <div class="thumb" style="left:658px;top:780px"><span role="img" aria-label="Screenshot of bar charts and gauges" style="background:linear-gradient(180deg,#f4f6f8,#d6dde3)"></span></div>
  <div class="thumb" style="left:746px;top:780px"><span role="img" aria-label="Screenshot of an analytics dashboard" style="background:linear-gradient(135deg,#dfe8f2,#7d96b3)"></span></div>
  <a class="read-more" href="#" style="left:739px;top:878px"><i></i>view all products</a>
</section>

<footer class="abs footer">
  <h4 class="foot-head" style="left:24px;width:116px">EUROPE</h4>
  <div class="foot-addr" style="left:24px">18 Harlow Row<br>Dunmere, DN4 2QT<br>Phone:+44(0)1632 960415<br>Email:eu@corvinsoft.example</div>
  <h4 class="foot-head" style="left:184px;width:116px">NORTH AMERICA</h4>
  <div class="foot-addr" style="left:184px">410 Meridian Park Dr, Suite 200<br>Calloway, TX 75099<br>Phone:(555) 014 3382<br>Email:us@corvinsoft.example</div>
  <h4 class="foot-head" style="left:360px;width:178px">OUR GOLD BUSINESS PARTNER</h4>
  <div class="abs partner-badge" role="img" aria-label="Partner badge"></div>
  <div class="abs foot-rule"></div>
  <p class="abs foot-text">Lorem ipsum dolor sit amet, consectetur adipiscing elit. Donec semper nisl eget ante vehicula at viverra est porta. Morbi eleifend, turpis eget vehicula porta, leo velit facilisis justo, quis vehicula velit erat nec est. Pellentesque habitant morbi tristique senectus et netus et malesuada fames ac turpis egestas. Pellentesque consequat est vel metus luctus commodo. In hac habitasse platea dictumst. Suspendisse justo ipsum,</p>

  <h4 class="abs touch">Get in touch</h4>
  <div class="field" style="top:51px;height:22px">Name</div>
  <div class="field" style="top:79px;height:22px">E-mail</div>
  <div class="field" style="top:107px;height:50px">Message</div>
  <div class="abs submit">SUBMIT</div>

  <div class="abs foot-bottom"></div>
  <div class="abs foot-links">Privacy Policy &nbsp;&nbsp;|&nbsp;&nbsp; Terms &amp; Conditions</div>
  <div class="abs copy">© Copyrights 2012 Corvin Soft</div>
</footer>
</body>
</html>
```